Luxury WordPress Website for CORALBASINS

I need a professional WordPress website for Coral Basins. The site should be modern, visually appealing, and user-friendly, reflecting the brand’s luxury and premium identity. It must include a homepage, product/service pages, contact form, and be responsive on both desktop and mobile devices. The design should allow for easy updates and integration of future content, while maintaining a polished and professional look.

Target Market(s)

swimmingpool & spa

Industry/Entity Type

Swimmingpool

Coding

Coded - Design and coding required

Font styles to use
Other font styles liked:
• HaboroSoft

Requirements
Must have
• Exclusive appearance
Nice to have
• • A logo that subtly incorporates water or pool elements. • A color palette that reflects luxury, elegance, and relaxation. • Clean and modern typography that is easy to read across all media. • Iconography or design elements that convey premium quality. • A versatile design that can be adapted for social media, merchandise, and promotional materials. • Optional: A tagline that emphasizes luxury and high-end pool experiences.

```html
<!DOCTYPE html>
<html lang="en">
<head>
<meta charset="utf-8">
<title>Coral Basins — Luxury Pools</title>
<link rel="stylesheet" href="https://fonts.googleapis.com/css2?family=Libre+Baskerville:wght@400;700&family=Inter:wght@400;500;600;700&display=swap">
<style>
:root{
  --teal:#4fa8c2;
  --teal-deep:#2f7fa6;
  --teal-soft:#e9f4f8;
  --ink:#1f2a33;
  --muted:#5b6670;
  --line:#d9e3e8;
  --white:#ffffff;
}
*{box-sizing:border-box;margin:0;padding:0}
html,body{width:1200px;height:5063px;overflow:hidden}
body{position:relative;background:var(--white);font-family:"Inter",sans-serif;color:var(--ink)}
.abs{position:absolute}
.serif{font-family:"Libre Baskerville",serif}
.ph{position:absolute;overflow:hidden}
.brand{display:flex;align-items:center;gap:10px;font-family:"Inter",sans-serif;font-weight:600;color:var(--teal-deep)}
.brand i{display:block;border-radius:50%;border:2px solid currentColor}

/* hero */
.hero-img{left:604px;top:0;width:590px;height:731px;border-bottom-left-radius:260px;background:linear-gradient(160deg,#dfe9ec 0%,#b9d2d8 35%,#8fc3cf 60%,#5fb2c9 80%,#cfe2e6 100%)}
.nav{left:604px;top:0;width:590px;height:82px;background:var(--teal);display:flex;align-items:center;gap:30px;padding-left:58px;font-size:13px;color:#fff}
.nav a{color:#fff;text-decoration:none}
.nav .on{border-bottom:2px solid #fff;padding-bottom:3px}
.nav .quote{margin-left:12px;background:#fff;color:var(--teal);border-radius:4px;padding:10px 22px;font-family:"Libre Baskerville",serif;font-size:13px}
.hero h1{left:94px;top:146px;font-size:46px;line-height:56px;font-weight:700;color:var(--ink)}
.hero h1 span{color:var(--teal)}
.hero p{left:94px;top:348px;width:440px;font-size:15.5px;line-height:21px;color:#3a4550}
.btn{position:absolute;display:flex;align-items:center;justify-content:center;gap:8px;font-family:"Libre Baskerville",serif;font-size:13px;border-radius:4px}
.btn-fill{background:var(--teal-deep);color:#fff}
.btn-line{border:1.5px solid var(--teal-deep);color:var(--teal-deep)}
.stat{position:absolute;top:540px;height:76px;background:#f5f8f9;border-radius:6px;padding:14px 16px}
.stat b{display:block;font-size:23px;font-weight:600}
.stat small{font-size:12px;color:var(--muted)}

/* headings */
.sec-title{position:absolute;left:0;width:1200px;text-align:center;font-family:"Libre Baskerville",serif;font-size:30px;font-weight:700}
.sec-title span{color:var(--teal)}
.rule{position:absolute;left:555px;width:90px;height:3px;background:var(--teal-deep)}
.lede{position:absolute;left:0;width:1200px;text-align:center;font-size:13px;line-height:20px;color:#3a4550}

/* about */
.about{left:0;top:753px;width:1196px;height:688px;background:var(--teal-soft)}
.about h3{left:110px;top:960px;font-size:18px;color:var(--teal)}
.about-copy{left:110px;top:1016px;width:430px;font-size:13.4px;line-height:22px;color:#3a4550}
.about-copy p+p{margin-top:22px}
.pill{border-radius:80px}

/* collections */
.col-card{top:1651px;height:315px;width:326px;border-radius:4px}
.col-card h4{position:absolute;left:24px;bottom:66px;font-family:"Libre Baskerville",serif;font-size:19px;color:#fff}
.col-card p{position:absolute;left:24px;right:20px;bottom:28px;font-size:10px;line-height:16px;color:#eaf6fa}

/* featured */
.tag{left:503px;top:2088px;width:194px;height:34px;border-radius:17px;background:var(--teal-soft);color:var(--teal-deep);font-family:"Libre Baskerville",serif;font-size:13px;display:flex;align-items:center;justify-content:center}
.tabs{left:320px;top:2306px;width:572px;height:38px;border-radius:19px;background:#f1f4f5;display:flex;align-items:center;padding:0 4px;font-size:11px;color:#44505a}
.tabs span{flex:1;text-align:center}
.tabs .on{background:var(--teal-deep);color:#fff;border-radius:15px;padding:8px 0;flex:0 0 104px}
.proj .cap{position:absolute;left:28px;bottom:20px;color:#fff;font-size:10px;line-height:16px}
.proj .cap b{display:block;font-family:"Libre Baskerville",serif;font-size:13px;font-weight:400}

/* services */
.services{left:6px;top:3067px;width:1194px;height:600px;background:linear-gradient(180deg,#2f7fa8 0%,#55a9c5 100%)}
.svc{position:absolute;top:3313px;width:222px;height:242px;background:#fff;border-radius:4px;text-align:center;padding:34px 18px 0}
.svc .ic{width:50px;height:50px;border-radius:50%;background:var(--teal);margin:0 auto 18px;display:flex;align-items:center;justify-content:center}
.svc h5{font-size:13px;font-weight:700;margin-bottom:12px;letter-spacing:.3px}
.svc p{font-size:11px;line-height:20px;color:#47525c}

/* contact */
.form-card{left:88px;top:3924px;width:516px;height:572px;background:#fff;border-radius:6px;box-shadow:0 4px 12px rgba(0,0,0,.12)}
.lbl{position:absolute;font-size:13px;color:#3a4550}
.field{position:absolute;height:38px;border:1px solid #b8c3c9;border-radius:3px;font-size:13px;color:#8a949b;padding:11px 12px}
.info-card{left:645px;top:3924px;width:474px;height:572px;background:#55a9c5;border-radius:6px;color:#fff}
.ci{position:absolute;left:34px;display:flex;gap:24px;font-size:13px;line-height:19px}
.ci .ib{width:44px;height:44px;border-radius:50%;background:#fff;display:flex;align-items:center;justify-content:center;flex:none}
.ci b{font-weight:600}
.soc{width:38px;height:38px;border-radius:50%;background:#fff}

/* footer */
.foot-bg{left:0;top:4600px;width:1200px;height:463px}
.fcol{position:absolute;top:4710px;color:#fff;font-size:13px;line-height:33px}
.fcol h6{font-family:"Libre Baskerville",serif;font-weight:400;font-size:13px;border-left:2px solid #fff;padding-left:12px;margin-bottom:6px;line-height:18px}
.fcol li{list-style:none;padding-left:4px}
.fcol li::before{content:"";display:inline-block;width:6px;height:6px;border-radius:50%;background:#cfeaf2;margin-right:10px;vertical-align:middle}
</style>
</head>
<body>

<!-- HERO -->
<section class="hero">
  <div class="ph hero-img" role="img" aria-label="Bright indoor spa with a round whirlpool tub beside floor-to-ceiling windows"></div>
  <nav class="abs nav">
    <a class="on">Home</a><a>About Us</a><a>Products</a><a>Contact Us</a>
    <span class="quote">Get a Quote</span>
  </nav>
  <div class="abs brand" style="left:92px;top:22px;font-size:14px"><i style="width:34px;height:34px"></i>Coral Basins</div>
  <h1 class="abs serif">EXPERIENCE <span style="color:var(--ink)"></span><br></h1>
  <h1 class="abs serif"><span>EXPERIENCE</span> THE<br>ART OF LUXURY<br>POOLS</h1>
  <p class="abs">Coral Basins menghadirkan kolam renang eksklusif dengan desain dan kualitas terbaik untuk hunian mewah Anda.</p>
  <div class="btn btn-fill" style="left:94px;top:448px;width:160px;height:54px">Explore Collections</div>
  <div class="btn btn-line" style="left:274px;top:448px;width:198px;height:54px">
    <svg width="16" height="16" viewBox="0 0 24 24" fill="none" stroke="currentColor" stroke-width="2"><path d="M22 16.9v3a2 2 0 0 1-2.2 2A19.8 19.8 0 0 1 2.1 4.2 2 2 0 0 1 4.1 2h3a2 2 0 0 1 2 1.7c.1 1 .4 1.9.7 2.8a2 2 0 0 1-.5 2.1L8 9.9a16 16 0 0 0 6 6l1.3-1.3a2 2 0 0 1 2.1-.4c.9.3 1.8.6 2.8.7a2 2 0 0 1 1.8 2z"/></svg>
    Request Consultation</div>
  <div class="stat" style="left:94px;width:132px"><b>500+</b><small>Pools Built</small></div>
  <div class="stat" style="left:238px;width:132px"><b>15+</b><small>Years Experience</small></div>
  <div class="stat" style="left:384px;width:144px"><b>100%</b><small>Satisfaction</small></div>
</section>

<!-- ABOUT -->
<section>
  <div class="abs about"></div>
  <h2 class="sec-title" style="top:806px">About <span>Coral Basins</span></h2>
  <div class="rule" style="top:850px;left:494px;width:212px"></div>
  <h3 class="abs serif about" style="background:none;left:110px;top:960px;width:auto;height:auto;font-size:18px;color:var(--teal);font-weight:400">Crafting Timeless Pool Experiences</h3>
  <div class="abs about-copy">
    <p>At Coral Basins, we don't just build swimming pools – we create aquatic masterpieces that transform your outdoor space into a luxury resort experience. With over a decade of expertise in premium pool construction, we combine innovative design, superior craftsmanship, and cutting-edge technology to deliver pools that exceed expectations.</p>
    <p>Every project is a testament to our commitment to excellence, using only the finest materials and employing master craftsmen who understand that your pool is more than just a feature – it's the centerpiece of your lifestyle.</p>
  </div>
  <div class="btn btn-fill" style="left:110px;top:1290px;width:218px;height:44px;border-radius:22px;background:var(--teal);font-size:12px">Learn More About Us &nbsp;→</div>
  <div class="ph pill" style="left:586px;top:895px;width:154px;height:308px;background:linear-gradient(180deg,#2f86c4,#7ab3cf)" role="img" aria-label="Woven loungers on a mosaic pool deck"></div>
  <div class="ph pill" style="left:762px;top:895px;width:140px;height:114px;background:linear-gradient(180deg,#f2efe8,#d8cdb9)" role="img" aria-label="Spa oils, stones and towels"></div>
  <div class="ph pill" style="left:762px;top:1071px;width:144px;height:310px;background:linear-gradient(180deg,#e8c9b5,#7b8a86)" role="img" aria-label="Guest relaxing at a poolside spa"></div>
  <div class="ph pill" style="left:934px;top:1003px;width:150px;height:310px;background:linear-gradient(180deg,#bfe3ef,#3fb0d2)" role="img" aria-label="Guest under a pool water fountain"></div>
  <div class="ph pill" style="left:596px;top:1221px;width:144px;height:172px;background:linear-gradient(180deg,#7aa95c,#c9d9de)" role="img" aria-label="Garden loungers beside tropical plants"></div>
</section>

<!-- COLLECTIONS -->
<section>
  <h2 class="sec-title" style="top:1494px">Our Pool <span>Collections</span></h2>
  <div class="rule" style="top:1548px;left:555px"></div>
  <p class="lede" style="top:1570px">Discover our signature pool designs, each crafted to elevate your outdoor living experience</p>
  <div class="ph col-card" style="left:96px;background:linear-gradient(180deg,#8d9a9c,#4f9fb5)" role="img" aria-label="Indoor infinity pool in a stone grotto">
    <h4>Infinity Pool</h4><p>Experience the illusion of water extending to the horizon with our stunning infinity edge designs</p></div>
  <div class="ph col-card" style="left:442px;background:linear-gradient(180deg,#5fa7dc,#6fa45a 55%,#1f8fc4)" role="img" aria-label="Resort pool framed by palm trees">
    <h4>Modern Pool</h4><p>Clean lines and contemporary aesthetics for the modern architectural vision.</p></div>
  <div class="ph col-card" style="left:786px;background:linear-gradient(180deg,#6b4a32,#c79c7e 60%,#e8d6c6)" role="img" aria-label="Guest resting during a spa massage">
    <h4>Spa Integration</h4><p>Seamless blend of relaxation and luxury through integrated spa features</p></div>
</section>

<!-- FEATURED -->
<section>
  <div class="abs tag">Check Our Collection</div>
  <h2 class="sec-title" style="top:2138px;font-weight:400">Featured Product</h2>
  <p class="lede" style="top:2209px">Explore our portfolio of kitchens, bathrooms, and luxury interiors designed for distinction. Each<br>project combines premium materials, precision engineering, and timeless design.</p>
  <div class="abs tabs"><span class="on">All Projects</span><span>Infinity Pool</span><span>SPA &amp; Jacuzzi</span><span>Resort Style</span><span>Outdoor</span></div>

  <div class="ph proj" style="left:94px;top:2416px;width:325px;height:236px;background:linear-gradient(180deg,#f2f2f0,#d9d6d0 60%,#3fa6c9)" role="img" aria-label="Deck chairs beside a white-edged pool">
    <div class="cap">Luxury Pool<b>Modern Infinity Edge</b>Palm Beach Estate</div></div>
  <div class="ph proj" style="left:94px;top:2674px;width:325px;height:236px;background:linear-gradient(180deg,#5f7b4a,#3a5a3a 50%,#2a9ac0)" role="img" aria-label="Tropical plants beside a garden pool">
    <div class="cap">Custom Pool<b>Natural Lagoon Design</b>Hillside Retreat</div></div>
  <div class="ph proj" style="left:440px;top:2463px;width:325px;height:376px;background:linear-gradient(160deg,#c79a6a,#3186c7 45%,#2a70b5)" role="img" aria-label="Woven loungers on blue mosaic tiles">
    <div class="cap">Rooftop Pool<b>Geometric Elegance</b>Urban Penthouse</div></div>
  <div class="ph proj" style="left:784px;top:2404px;width:325px;height:236px;background:linear-gradient(180deg,#2f5a48,#6b7a74 55%,#4d9fa8)" role="img" aria-label="Sun loungers on a shaded pool terrace">
    <div class="cap">Luxury Pool<b>Modern Infinity Edge</b>Palm Beach Estate</div></div>
  <div class="ph proj" style="left:784px;top:2662px;width:325px;height:236px;background:linear-gradient(180deg,#4f86b8,#6aa3c2 50%,#1f96c8)" role="img" aria-label="Infinity pool facing the ocean at dusk">
    <div class="cap">Custom Pool<b>Natural Lagoon Design</b>Hillside Retreat</div></div>

  <div class="btn btn-fill" style="left:523px;top:2961px;width:163px;height:43px;font-size:12px">View All Product</div>
</section>

<!-- SERVICES -->
<section>
  <div class="abs services"></div>
  <h2 class="sec-title" style="top:3133px;color:#fff">Our Premium Services</h2>
  <p class="lede" style="top:3226px;color:#fff;font-size:15px;line-height:21px">We offer a complete range of high-end pool and spa solutions,<br>from custom design to expert installation and maintenance.</p>
  <div class="svc" style="left:112px"><div class="ic"><svg width="24" height="24" viewBox="0 0 24 24" fill="none" stroke="#fff" stroke-width="1.8"><circle cx="12" cy="12" r="9"/><circle cx="8" cy="10" r="1.2"/><circle cx="12" cy="7.5" r="1.2"/><circle cx="16" cy="10" r="1.2"/></svg></div>
    <h5>Custom Design</h5><p>We use only the finest materials sourced from premium suppliers worldwide</p></div>
  <div class="svc" style="left:366px"><div class="ic"><svg width="24" height="24" viewBox="0 0 24 24" fill="none" stroke="#fff" stroke-width="1.8"><path d="M12 3c3 4 6 7 6 11a6 6 0 0 1-12 0c0-4 3-7 6-11z"/></svg></div>
    <h5>Luxury Spas</h5><p>Premium spa installations with advanced hydrotherapy features for the ultimate relaxation experience.</p></div>
  <div class="svc" style="left:619px"><div class="ic"><svg width="24" height="24" viewBox="0 0 24 24" fill="none" stroke="#fff" stroke-width="1.8"><rect x="6" y="3" width="12" height="18" rx="2"/><path d="M9 15h6M9 18h6"/></svg></div>
    <h5>Expert Installation</h5><p>Precision engineering and craftsmanship ensuring your pool is built to the highest standards.</p></div>
  <div class="svc" style="left:873px"><div class="ic"><svg width="24" height="24" viewBox="0 0 24 24" fill="none" stroke="#fff" stroke-width="1.8"><path d="M12 3l7.8 4.5v9L12 21l-7.8-4.5v-9z"/><circle cx="12" cy="12" r="3"/></svg></div>
    <h5>Maintenance</h5><p>Comprehensive maintenance services to keep your investment pristine and functioning perfectly.</p></div>
</section>

<!-- CONTACT -->
<section>
  <p class="lede" style="top:3728px;color:var(--teal);font-size:14px">Contact Us</p>
  <h2 class="sec-title" style="top:3766px;font-size:38px;font-weight:400">Let's Work <span>Together</span></h2>
  <p class="lede" style="top:3852px;font-size:14px">Interested in our products? Contact us for quotes or partnership opportunities.</p>

  <div class="abs form-card"></div>
  <h4 class="abs serif" style="left:114px;top:3954px;font-size:17px;font-weight:400;color:var(--teal-deep)">Request Service</h4>
  <span class="lbl" style="left:118px;top:4018px">Name</span>
  <div class="field" style="left:118px;top:4044px;width:214px">Your name</div>
  <span class="lbl" style="left:362px;top:4018px">Email</span>
  <div class="field" style="left:362px;top:4044px;width:212px">Your Email</div>
  <span class="lbl" style="left:118px;top:4098px">Phone</span>
  <div class="field" style="left:118px;top:4124px;width:214px">Your phone number</div>
  <span class="lbl" style="left:362px;top:4098px">Services of interest</span>
  <div class="field" style="left:362px;top:4124px;width:212px">Services<span style="float:right;color:#333">▾</span></div>
  <span class="lbl" style="left:118px;top:4178px">Budget Estimasi</span>
  <div class="field" style="left:118px;top:4204px;width:456px;padding-left:18px">Input Subject</div>
  <span class="lbl" style="left:118px;top:4258px">Service Request</span>
  <div class="field" style="left:118px;top:4284px;width:456px;height:112px;padding-left:18px">Describe the service your need</div>
  <div class="btn" style="left:118px;top:4434px;width:456px;height:42px;background:var(--teal);color:#fff;font-family:Inter,sans-serif;font-size:13px">Submit Request
    <svg width="14" height="14" viewBox="0 0 24 24" fill="none" stroke="#fff" stroke-width="2"><path d="M22 2L11 13M22 2l-7 20-4-9-9-4z"/></svg></div>

  <div class="abs info-card"></div>
  <div class="abs brand" style="left:698px;top:3970px;color:#fff;font-size:22px;font-weight:500"><i style="width:84px;height:84px;border-width:2px"></i>Coral Basins</div>
  <h4 class="abs serif" style="left:680px;top:4104px;color:#fff;font-size:16px;font-weight:400">Contact Information</h4>
  <div class="ci" style="left:680px;top:4166px"><span class="ib"><svg width="18" height="18" viewBox="0 0 24 24" fill="none" stroke="#55a9c5" stroke-width="2"><path d="M22 16.9v3a2 2 0 0 1-2.2 2A19.8 19.8 0 0 1 2.1 4.2 2 2 0 0 1 4.1 2h3a2 2 0 0 1 2 1.7c.1 1 .4 1.9.7 2.8a2 2 0 0 1-.5 2.1L8 9.9a16 16 0 0 0 6 6l1.3-1.3a2 2 0 0 1 2.1-.4c.9.3 1.8.6 2.8.7a2 2 0 0 1 1.8 2z"/></svg></span>
    <div><b>Call Us</b><br>+1 555 014 2290<br><span style="opacity:.75">Mon-Fri 8:00 AM - 6:00 PM MST</span></div></div>
  <div class="ci" style="left:680px;top:4254px"><span class="ib"><svg width="18" height="18" viewBox="0 0 24 24" fill="none" stroke="#55a9c5" stroke-width="2"><rect x="3" y="5" width="18" height="14" rx="2"/><path d="M3 7l9 6 9-6"/></svg></span>
    <div><b>Email Us</b><br>info@coralbasins.example<br>studio@coralbasins.example</div></div>
  <div class="ci" style="left:680px;top:4342px"><span class="ib"><svg width="18" height="18" viewBox="0 0 24 24" fill="none" stroke="#55a9c5" stroke-width="2"><path d="M12 22s7-7 7-12a7 7 0 0 0-14 0c0 5 7 12 7 12z"/><circle cx="12" cy="10" r="2.5"/></svg></span>
    <div><b>Address</b><br>48 Lagoon Drive, Bayview, CA 90000</div></div>
  <b class="abs" style="left:686px;top:4396px;color:#fff;font-size:13px;font-weight:600">Follow us</b>
  <div class="abs" style="left:686px;top:4428px;display:flex;gap:30px"><span class="soc"></span><span class="soc"></span><span class="soc"></span><span class="soc"></span></div>
</section>

<!-- FOOTER -->
<footer>
  <svg class="abs foot-bg" viewBox="0 0 1200 463" preserveAspectRatio="none" aria-hidden="true">
    <path d="M0 70 Q600 -60 1200 70 V463 H0z" fill="#55a9c5"/>
    <rect x="0" y="373" width="1200" height="90" fill="#4ea2bf"/>
  </svg>
  <div class="abs brand" style="left:82px;top:4718px;color:#fff;font-size:15px;font-weight:500"><i style="width:62px;height:62px"></i>Coral Basins</div>
  <p class="abs" style="left:76px;top:4818px;width:300px;color:#fff;font-size:13px;line-height:20px">Coral Basins presents exclusive swimming pools with the best design and quality for your luxury residence.</p>
  <div class="abs" style="left:76px;top:4908px;display:flex;gap:20px"><span class="soc" style="width:30px;height:30px;background:none;border:2px solid #fff"></span><span class="soc" style="width:30px;height:30px;background:none;border:2px solid #fff"></span><span class="soc" style="width:30px;height:30px;background:none;border:2px solid #fff"></span><span class="soc" style="width:30px;height:30px;background:none;border:2px solid #fff"></span></div>
  <div class="fcol" style="left:414px"><h6>Quick Links</h6><ul><li>Home</li><li>About Us</li><li>Products</li><li>Contact</li></ul></div>
  <div class="fcol" style="left:620px"><h6>Services</h6><ul><li>Custom Pool Design</li><li>Pool Installation</li><li>Luxury Spas</li><li>Maintenance</li></ul></div>
  <div class="fcol" style="left:844px;line-height:20px"><h6>Contact</h6>
    <p style="width:230px;margin-top:22px">Get inspiration and exclusive offers straight to your email.</p>
    <div style="display:flex;margin-top:12px"><span style="width:194px;height:34px;background:#fff;color:#aab3b8;font-size:11px;padding:8px 12px;border-radius:3px 0 0 3px">Email Anda</span><span style="width:56px;height:34px;background:var(--teal-deep);font-size:11px;display:flex;align-items:center;justify-content:center;border-radius:0 3px 3px 0">Daftar</span></div>
  </div>
  <p class="abs" style="left:0;top:5012px;width:1200px;text-align:center;color:#e3f2f7;font-size:11px">© 2025 CORAL BASINS. All rights reserved.</p>
</footer>

</body>
</html>
```